Used Semi Truck Website Redesign

We are redoing the website backend and would like to also do a front end redesign. I would like a Mobile and Desktop mockup for each page. The website has more mobile visitors than desktop visitors. Our competitor is http://www.haulwaybazaar.example. We don't want to copy them exactly but we want a site that looks more like that. We need the functionality of that site. One big difference is that we also sell parts and trailers.

We need a redesign for front page, product detail page, search result page, content page. It is very important that the site is very easy to use on mobile devices. Our target audience is Truck drivers.

Feel free to use demo fonts stock images, and icons. We will purchase necessary 3rd party media when a winner is chosen.

Target Market(s)

People who want to buy used trucks.

Coding

Coded - Design and coding required

Number of Pages Required

5+ page

Requirements
Must have
• Mockup for Desktop and Mobile pages.

```html
<!DOCTYPE html>
<html lang="en">
<head>
<meta charset="utf-8">
<title>Rigline Trucks</title>
<link href="https://fonts.googleapis.com/css2?family=Open+Sans:wght@400;600;700&display=swap" rel="stylesheet">
<style>
:root{
  --navy:#1f3050;
  --navy-dark:#15233d;
  --plum:#594869;
  --slate:#959bb3;
  --sky:#2ea7e0;
  --band:#eef5fc;
  --text:#333a45;
  --muted:#8a8f99;
  --line:#c9ccd2;
  --white:#ffffff;
}
*{box-sizing:border-box;margin:0;padding:0}
html,body{width:1200px;height:2281px;overflow:hidden}
body{font-family:"Open Sans",sans-serif;color:var(--text);background:var(--white);position:relative}
.wrap{width:934px;margin:0 auto;position:relative}
a{color:inherit;text-decoration:none}

.site-header{height:84px}
.site-header .wrap{height:84px;display:flex;align-items:center;justify-content:space-between}
.brand{font-size:44px;color:var(--navy);font-weight:400;letter-spacing:-.5px}
.quick-links{display:flex;gap:9px}
.quick-links a{border:2px solid var(--line);height:38px;padding:0 14px;display:flex;align-items:center;gap:7px;font-size:16px;color:#7c828c}
.quick-links svg{width:12px;height:12px}

.main-nav{background:var(--navy);height:41px}
.main-nav .wrap{display:flex;height:41px}
.main-nav a{color:var(--white);font-size:13px;font-weight:600;display:flex;align-items:center;justify-content:center;width:191px}
.main-nav a.active{background:var(--navy-dark)}

.hero{height:489px;position:relative;background:linear-gradient(180deg,#8fb9e0 0%,#b9d3ea 40%,#8f9a86 62%,#6d7a8a 100%)}
.hero-photo{position:absolute;inset:0;background:linear-gradient(100deg,rgba(255,255,255,0) 15%,rgba(230,236,244,.55) 30%,rgba(40,90,170,.35) 50%,rgba(230,236,244,.35) 70%,rgba(0,0,0,0) 90%)}
.hero-arrow{position:absolute;top:228px;width:24px;height:32px;background:rgba(120,130,140,.6);display:flex;align-items:center;justify-content:center}
.hero-arrow.left{left:0}.hero-arrow.right{right:0}
.search-panel{position:absolute;left:0;right:0;top:354px;height:135px;background:rgba(200,214,232,.55)}
.search-grid{display:grid;grid-template-columns:221px 220px 221px 219px;column-gap:17.6px;row-gap:17px;padding-top:20px}
.field{height:38px;background:var(--white);font-size:12px;color:#8d929a;display:flex;align-items:center;justify-content:space-between;padding:0 16px}
.field svg{width:9px;height:6px}
.btn-search{height:38px;background:var(--navy);color:var(--white);font-size:13px;font-weight:600;display:flex;align-items:center;justify-content:center}
.adv-link{font-size:12px;color:var(--white);text-decoration:underline;display:flex;align-items:center;padding-left:16px}

.categories{padding-top:40px}
.cat-row{display:grid;grid-template-columns:repeat(4,1fr);gap:17px}
.cat{background:var(--plum);height:128px;text-align:center;color:var(--white);padding:22px 18px 0}
.cat h3{font-size:16px;font-weight:700;line-height:21px;text-transform:uppercase}
.cat p{font-size:11px;color:#d7d0de;margin-top:7px;line-height:16px}

.section-head{display:flex;justify-content:space-between;align-items:center;height:44px}
.section-head h2{font-size:24px;font-weight:400;color:var(--navy)}
.pager{display:flex;gap:7px}
.pager span{width:22px;height:22px;border:1px solid var(--navy);display:flex;align-items:center;justify-content:center}
.pager.light span{border-color:#aeb3bb}
.pager svg{width:7px;height:10px}

.featured{margin-top:28px}
.ads{display:grid;grid-template-columns:repeat(4,1fr);gap:17px;margin-top:7px}
.ad-photo{height:158px}
.ad h4{font-size:14px;font-weight:400;text-align:center;margin-top:12px;color:var(--text)}
.ad p{font-size:11px;color:var(--muted);text-align:center;line-height:17px;margin-top:6px;padding:0 6px}

.info-band{position:absolute;top:1148px;left:0;right:0;height:264px;background:var(--band)}
.info-band .wrap{display:flex;gap:11px;padding-top:32px}
.dealer-box{width:338px;height:201px;background:var(--slate);padding:16px 24px;color:var(--white)}
.dealer-box h3{font-size:24px;font-weight:400}
.dealer-box p{font-size:11px;line-height:16px;margin-top:2px}
.dealer-box .field{margin-top:14px;width:287px;height:38px;font-size:11px;padding:0 18px}
.dealer-box .btn{margin-top:12px;width:121px;height:36px;background:var(--navy);font-size:12px;font-weight:600;display:flex;align-items:center;justify-content:center}
.feed-box{width:336px;height:201px;background:var(--sky);color:var(--white);padding:16px 24px}
.feed-box h3{font-size:24px;font-weight:400}
.feed-box .handle{font-size:12px;margin-top:14px}
.feed-box .post{font-size:12px;line-height:19px;margin-top:14px}
.feed-actions{display:flex;gap:14px;align-items:center;margin-top:16px;font-size:12px}
.feed-actions svg{width:11px;height:10px}
.promo{width:239px;height:201px;background:linear-gradient(180deg,#1d5fa8 0%,#4c8fd0 45%,#b6c9da 100%);border:1px solid #1a3f6d}

.stories{position:absolute;top:1466px;left:0;right:0}
.story-row{display:grid;grid-template-columns:repeat(3,1fr);gap:23px;margin-top:13px}
.story-photo{height:179px;position:relative}
.play{position:absolute;left:50%;top:50%;width:40px;height:40px;margin:-20px 0 0 -20px;border-radius:50%;background:var(--white);display:flex;align-items:center;justify-content:center}
.story h4{font-size:15px;font-weight:400;line-height:21px;margin-top:17px;color:var(--text)}
.story p{font-size:11px;line-height:17px;color:var(--muted);margin-top:8px;text-align:justify}
.story a{display:inline-block;font-size:11px;color:var(--text);text-decoration:underline;margin-top:14px}

.directory{position:absolute;top:1926px;left:0;right:0;height:264px;background:var(--band)}
.directory .wrap{display:flex;gap:22px;padding-top:32px}
.dir-card{background:var(--white);height:199px;padding:18px 14px;flex:1}
.dir-card h3{font-size:24px;font-weight:400;color:var(--navy);white-space:nowrap}
.dir-cols{display:flex;gap:22px;margin-top:10px}
.dir-cols ul{list-style:none;font-size:11px;line-height:20px;color:var(--text)}
.dir-cols li::before{content:"• ";}
.dir-cols li.more::before{content:""}

.site-footer{position:absolute;top:2190px;left:0;right:0;height:91px}
.site-footer .wrap{display:flex;justify-content:space-between;padding-top:24px}
.foot-links{font-size:11px;color:var(--text)}
.foot-links span{margin:0 7px;color:var(--muted)}
.copy{font-size:11px;color:var(--text);margin-top:14px}
.social{display:flex;gap:7px;margin-top:14px}
.social span{width:26px;height:26px;border-radius:50%}
</style>
</head>
<body>

<header class="site-header">
  <div class="wrap">
    <div class="brand">Rigline Trucks</div>
    <nav class="quick-links">
      <a href="#"><svg viewBox="0 0 12 12"><circle cx="5" cy="5" r="3.5" fill="none" stroke="#7c828c" stroke-width="1.6"/><path d="M7.5 7.5L11 11" stroke="#7c828c" stroke-width="1.6"/></svg>Find</a>
      <a href="#"><svg viewBox="0 0 12 12"><path d="M1 1h5l5 5-5 5-5-5z" fill="#7c828c"/></svg>Sell</a>
      <a href="#"><svg viewBox="0 0 12 12"><path d="M1 11h10M2 10V6M5 10V3M8 10V5" stroke="#7c828c" stroke-width="1.6"/></svg>Research</a>
    </nav>
  </div>
</header>

<nav class="main-nav">
  <div class="wrap">
    <a class="active" href="#">MYTRADER</a>
    <a href="#">FIND A DEALER</a>
    <a href="#">DEALER LOGIN</a>
    <a href="#">LOGIN</a>
    <a href="#">REGISTER</a>
  </div>
</nav>

<section class="hero">
  <div class="hero-photo" role="img" aria-label="Photo of a chrome semi truck with blue stripe hauling a flatbed on a desert highway"></div>
  <span class="hero-arrow left"><svg width="8" height="14" viewBox="0 0 8 14"><path d="M7 1L1 7l6 6" stroke="#fff" stroke-width="1.5" fill="none"/></svg></span>
  <span class="hero-arrow right"><svg width="8" height="14" viewBox="0 0 8 14"><path d="M1 1l6 6-6 6" stroke="#fff" stroke-width="1.5" fill="none"/></svg></span>
  <div class="search-panel">
    <div class="wrap search-grid">
      <div class="field">Keyword</div>
      <div class="field">Select Class<svg viewBox="0 0 9 6"><path d="M1 1l3.5 3.5L8 1" stroke="#8d929a" fill="none"/></svg></div>
      <div class="field">Select Category<svg viewBox="0 0 9 6"><path d="M1 1l3.5 3.5L8 1" stroke="#8d929a" fill="none"/></svg></div>
      <div class="field">Select a Make<svg viewBox="0 0 9 6"><path d="M1 1l3.5 3.5L8 1" stroke="#8d929a" fill="none"/></svg></div>
      <div class="field">Zipcode</div>
      <div class="field">Any Distance<svg viewBox="0 0 9 6"><path d="M1 1l3.5 3.5L8 1" stroke="#8d929a" fill="none"/></svg></div>
      <div class="btn-search">QUICK SEARCH</div>
      <a class="adv-link" href="#">Advanced Search</a>
    </div>
  </div>
</section>

<section class="categories">
  <div class="wrap cat-row">
    <div class="cat"><h3>Find Heavy Duty Trucks for Sale</h3><p>What Type Heavy Duty Truck do you need?</p></div>
    <div class="cat"><h3>Find Medium Duty Trucks for Sale</h3><p>What Type of Medium Duty Truck do you need?</p></div>
    <div class="cat"><h3>Find Light Duty Trucks for Sale</h3><p>What Type of Light Duty Truck do you need?</p></div>
    <div class="cat"><h3>Find Truck Trailers for Sale</h3><p>What Type of Trailer do you need?</p></div>
  </div>
</section>

<section class="featured">
  <div class="wrap">
    <div class="section-head">
      <h2>Featured Ads</h2>
      <div class="pager"><span><svg viewBox="0 0 7 10"><path d="M6 1L2 5l4 4" stroke="#1f3050" fill="none" stroke-width="1.4"/></svg></span><span><svg viewBox="0 0 7 10"><path d="M1 1l4 4-4 4" stroke="#1f3050" fill="none" stroke-width="1.4"/></svg></span></div>
    </div>
    <div class="ads">
      <div class="ad"><div class="ad-photo" role="img" aria-label="Photo of a white cutaway service van" style="background:linear-gradient(180deg,#9a9d9f,#e4e6e8 50%,#4d4f52)"></div><h4>2016 Forden Transa Cutaway</h4><p>Cutaway-Cube Van, Utility Truck - Service Truck<br>$37,900.00 - &nbsp;Phoenix, AZ</p></div>
      <div class="ad"><div class="ad-photo" role="img" aria-label="Photo of a red box truck with white cargo body" style="background:linear-gradient(180deg,#5f9ad8,#e8e6e0 45%,#b9352f 70%,#6b6a5c)"></div><h4>2016 Forden Transa Cutaway</h4><p>Cutaway-Cube Van, Utility Truck - Service Truck<br>$37,900.00 - &nbsp;Phoenix, AZ</p></div>
      <div class="ad"><div class="ad-photo" role="img" aria-label="Photo of a red dump truck on gravel" style="background:linear-gradient(180deg,#d6e3ef,#c7322f 50%,#8f8a80)"></div><h4>2016 Forden Transa Cutaway</h4><p>Cutaway-Cube Van, Utility Truck - Service Truck<br>$37,900.00 - &nbsp;Phoenix, AZ</p></div>
      <div class="ad"><div class="ad-photo" role="img" aria-label="Photo of a white enclosed cargo trailer under a carport" style="background:linear-gradient(180deg,#3a3c3e,#d8dadc 45%,#5d6064)"></div><h4>2016 Forden Transa Cutaway</h4><p>Cutaway-Cube Van, Utility Truck - Service Truck<br>$37,900.00 - &nbsp;Phoenix, AZ</p></div>
    </div>
  </div>
</section>

<section class="info-band">
  <div class="wrap">
    <div class="dealer-box">
      <h3>Find a Dealer</h3>
      <p>Find Commercial Truck dealers by name, make and location.</p>
      <div class="field">Zipcode</div>
      <div class="btn">FIND A DEALER</div>
    </div>
    <div class="feed-box">
      <h3>Social Feed</h3>
      <p class="handle">Haulway Bazaar @HaulwayBazaar</p>
      <p class="post">Day #6 Snow Day Face: Show off your best Snow Day impression for everyone to see! #15DaysofPhotos https://hb.example/p/21</p>
      <div class="feed-actions">
        <svg viewBox="0 0 11 10"><path d="M1 1h9v6H4L1 9z" fill="#fff"/></svg>
        <svg viewBox="0 0 11 10"><path d="M1 4V2h8M7 0l2 2-2 2M10 6v2H2M4 10L2 8l2-2" stroke="#fff" fill="none" stroke-width="1.2"/></svg>
        <svg viewBox="0 0 11 10"><path d="M10 4L6 0v2C2 2 1 5 1 9c1-3 3-4 5-4v2z" fill="#fff"/></svg>
        <span>10 Dec, 2016</span>
      </div>
    </div>
    <div class="promo" role="img" aria-label="Dealer advertisement banner with dealership photo and delivery trucks"></div>
  </div>
</section>

<section class="stories">
  <div class="wrap">
    <div class="section-head">
      <h2>Find a Dealer</h2>
      <div class="pager light"><span><svg viewBox="0 0 7 10"><path d="M6 1L2 5l4 4" stroke="#8a8f99" fill="none" stroke-width="1.4"/></svg></span><span><svg viewBox="0 0 7 10"><path d="M1 1l4 4-4 4" stroke="#8a8f99" fill="none" stroke-width="1.4"/></svg></span></div>
    </div>
    <div class="story-row">
      <article class="story"><div class="story-photo" role="img" aria-label="Photo of a travel trailer parked among green trees" style="background:linear-gradient(180deg,#3f8de0,#6aa0c8 35%,#4f8a3c 65%,#9aa394)"></div><h4>Donec scelerisque felis at ante rhoncus, non mattis nulla facilisis</h4><p>Integer gravida risus risus, in imperdiet leo convallis sed. Aenean lobortis neque, vitae faucibus lorem. Nulla dignissim tempus nisi, sed lobortis velit faucibus at. Fusce vel rutrum erat. Vivamus blandit interdum egestas.</p><a href="#">READ MORE</a></article>
      <article class="story"><div class="story-photo" role="img" aria-label="Photo of a tanker truck on a highway past green fields" style="background:linear-gradient(180deg,#b9cfe4,#8aa47a 40%,#9a9c9a 65%,#79a548)"></div><h4>Donec scelerisque felis at ante rhoncus, non mattis nulla facilisis</h4><p>Integer gravida risus risus, in imperdiet leo convallis sed. Aenean lobortis neque, vitae faucibus lorem. Nulla dignissim tempus nisi, sed lobortis velit faucibus at. Fusce vel rutrum erat. Vivamus blandit interdum egestas.</p><a href="#">READ MORE</a></article>
      <article class="story"><div class="story-photo" role="img" aria-label="Video still of a red semi truck hauling a trailer at dusk" style="background:linear-gradient(180deg,#3a4350,#6e7580 45%,#7a3a36 65%,#2a2d31)"><span class="play"><svg width="14" height="16" viewBox="0 0 14 16"><path d="M1 1l12 7-12 7z" fill="#2a2d31"/></svg></span></div><h4>Donec scelerisque felis at ante rhoncus, non mattis nulla facilisis</h4><p>Integer gravida risus risus, in imperdiet leo convallis sed. Aenean lobortis neque, vitae faucibus lorem. Nulla dignissim tempus nisi, sed lobortis velit faucibus at. Fusce vel rutrum erat. Vivamus blandit interdum egestas.</p><a href="#">READ MORE</a></article>
    </div>
  </div>
</section>

<section class="directory">
  <div class="wrap">
    <div class="dir-card">
      <h3>Trucks for sale by State</h3>
      <div class="dir-cols">
        <ul><li>Alabama</li><li>Alaska</li><li>Arizona</li><li>Arkansas</li><li>California</li><li>Colorado</li></ul>
        <ul><li>Connecticut</li><li>Delaware</li><li>Florida</li><li>Georgia</li><li>Hawaii</li><li>Idaho</li></ul>
        <ul><li>Illinois</li><li>Indiana</li><li>Iowa</li><li>Kansas</li><li>Kentucky</li><li class="more">View All &nbsp;››</li></ul>
      </div>
    </div>
    <div class="dir-card">
      <h3>Trucks for sale by Make</h3>
      <div class="dir-cols">
        <ul><li>Forden</li><li>Freightwell</li><li>Chevrane</li><li>Peterhaul</li><li>Interhaul</li><li>Kenridge</li></ul>
        <ul><li>Ramwell</li><li>Gentrux</li><li>Izumo</li><li>Mackley</li><li>Voltar</li><li>Dorge</li></ul>
        <ul><li>Hinata</li><li>Sterlane</li><li>Meridian-Benn</li><li>Nissaro</li></ul>
      </div>
    </div>
    <div class="dir-card">
      <h3>Resource Advertisers</h3>
      <div class="dir-cols">
        <ul><li>Insurance</li><li>Jobs &amp; Training</li><li>Vehicle History</li><li>Truck Bodies</li><li>Finance/Lease</li><li>Truck Parts</li></ul>
        <ul><li>Steel Buildings</li><li>Fuel Management</li><li>Shipping &amp; Transport</li><li class="more">&nbsp;&nbsp;View All &nbsp;››</li></ul>
      </div>
    </div>
  </div>
</section>

<footer class="site-footer">
  <div class="wrap">
    <div>
      <p class="foot-links">MyTrader<span>|</span>Find a Dealer<span>|</span>Dealer Login<span>|</span>Login<span>|</span>Register</p>
      <p class="copy">Copyright © 2016 &nbsp;Company name. &nbsp;All rights reserved.</p>
    </div>
    <div class="social">
      <span style="background:#3b5a9a"></span>
      <span style="background:#2ea7e0"></span>
      <span style="background:#1a76b4"></span>
      <span style="background:#dc4a38"></span>
    </div>
  </div>
</footer>

</body>
</html>
```